Product Label Design

Need a product design for our Epsom salt product, needs to have a luxurious simple feel to it. The picture attached is our brand and wordage on it, the bag we think should be a stand up bag that should be offwhite/creme color. The other picture are products that we like. We updated the packaging to be a Kraft tube box, please see the attached photo for dimensions.

```html
<!DOCTYPE html>
<html lang="en">
<head>
<meta charset="utf-8">
<title>VELA Uplift – Epsom Salt Pouch Label</title>
<link rel="stylesheet" href="https://fonts.googleapis.com/css2?family=Noto+Serif:wght@400;500&family=Montserrat:wght@500&display=swap">
<style>
  :root {
    --backdrop: #ece8e2;
    --pouch: #efe9e1;
    --pouch-edge: #e2dbd1;
    --frame: #c2b8ab;
    --ink-dark: #3b3936;
    --ink: #4a4540;
    --rule: #d2c9be;
    --botanical-tone: rgba(214, 200, 182, 0.38);
    --botanical-fade: rgba(239, 233, 225, 0);
  }
  * { margin: 0; padding: 0; box-sizing: border-box; }
  html, body {
    width: 1200px; height: 805px; overflow: hidden;
    background: var(--backdrop);
  }
  .pouch {
    position: absolute; left: 341px; top: 30px;
    width: 518px; height: 745px;
    background: var(--pouch);
    border: 1px solid var(--pouch-edge);
    border-radius: 12px 12px 18px 18px;
    overflow: hidden;
  }
  .pouch__zipper {
    position: absolute; left: 24px; right: 24px; top: 86px;
    height: 6px;
    border-top: 1px solid var(--pouch-edge);
    border-bottom: 1px solid var(--pouch-edge);
  }
  .botanical {
    position: absolute; z-index: 1;
  }
  .botanical--upper-right {
    left: 370px; top: 140px; width: 148px; height: 360px;
    background: radial-gradient(ellipse 50% 50% at 55% 40%, var(--botanical-tone), var(--botanical-fade));
  }
  .botanical--lower-left {
    left: 10px; top: 380px; width: 180px; height: 365px;
    background: radial-gradient(ellipse 50% 50% at 45% 50%, var(--botanical-tone), var(--botanical-fade));
  }
  .label-frame {
    position: absolute; z-index: 2;
    left: 50px; top: 164px;
    width: 414px; height: 531px;
    border: 1px solid var(--frame);
    outline: 1px solid var(--frame);
    outline-offset: -5px;
  }
  .label-copy { position: absolute; inset: 0; z-index: 3; }
  .brand {
    position: absolute; left: 0; right: 0; top: 206px;
    text-align: center;
    font-family: "Noto Serif", serif; font-weight: 400;
    font-size: 68px; line-height: 1; letter-spacing: 2px;
    color: var(--ink-dark);
  }
  .variant {
    position: absolute; left: 0; right: 0; top: 298px;
    text-align: center;
    font-family: "Montserrat", sans-serif; font-weight: 500;
    font-size: 14px; letter-spacing: 4px;
    color: var(--ink-dark);
  }
  .divider {
    position: absolute; left: 149px; top: 363px;
    width: 220px; height: 1px; background: var(--rule);
  }
  .ingredients {
    position: absolute; left: 0; right: 0; top: 407px;
    list-style: none; text-align: center;
    font-family: "Noto Serif", serif; font-size: 14.5px;
    line-height: 24.7px; color: var(--ink);
  }
  .net-weight {
    position: absolute; left: 0; right: 0; top: 643px;
    text-align: center;
    font-family: "Noto Serif", serif; font-weight: 500;
    font-size: 14.5px; letter-spacing: 0.3px;
    color: var(--ink);
  }
</style>
</head>
<body>
  <div class="pouch">
    <div class="pouch__zipper"></div>
    <div class="botanical botanical--upper-right" role="img" aria-label="Fine line botanical drawing of lilies and leaves"></div>
    <div class="botanical botanical--lower-left" role="img" aria-label="Fine line botanical drawing of lilies, buds and leaves"></div>
    <div class="label-frame"></div>

    <div class="label-copy">
      <h1 class="brand">VELA</h1>
      <p class="variant">UPLIFT</p>
      <div class="divider"></div>
      <ul class="ingredients">
        <li>US Sourced Pure Epsom Slat</li>
        <li>(Magnesium Sulfate)</li>
        <li>Abies Sibirica</li>
        <li>Fib Balsam</li>
      </ul>
      <p class="net-weight">NET WT. 3LBS (1360G)</p>
    </div>
  </div>
</body>
</html>
```